Looking for a modern, Professional business card design

We have a simple business card, but are looking for a more modern, professional look. A sample of the basic card is attached as well as the logo. We would also like to add that we offer:
Struggling with your finances?
- Learn to become debt free
- Discover the power of cash
- Control your money instead of it controlling you
Let us help you achieve a new level of financial freedom!
Also, we would like to have a "SPECIAL OFFER!: FREE 30 minute consultation"
Financial Planning

```html
<!DOCTYPE html>
<html lang="en">
<head>
<meta charset="utf-8">
<title>Steady Ledger Coaching – Business Card</title>
<link rel="stylesheet" href="https://fonts.googleapis.com/css2?family=Roboto:wght@400;500;700&family=Roboto+Condensed:wght@700&family=Archivo+Black&display=swap">
<style>
  :root {
    --page: #2a2a2a;
    --card: #ffffff;
    --green: #2f9e44;
    --green-band: #34a043;
    --green-light: #9acd3c;
    --green-dark: #3d8f3a;
    --ink: #111111;
    --grey: #555555;
    --rule: #9a9a9a;
    --white: #ffffff;
  }
  * { box-sizing: border-box; margin: 0; padding: 0; }
  html, body { width: 1200px; height: 987px; overflow: hidden; }
  body {
    position: relative;
    background: var(--page);
    font-family: "Roboto", Arial, sans-serif;
  }
  .card {
    position: absolute;
    left: 293px;
    width: 615px;
    height: 352px;
    overflow: hidden;
  }
  .card--front { top: 123px; background: var(--card); }
  .card--back {
    top: 499px;
    background: radial-gradient(ellipse 70% 80% at 48% 40%, var(--green-light) 0%, #6fb83a 45%, var(--green-dark) 100%);
  }

  /* front */
  .brand {
    position: absolute;
    right: 36px;
    top: 50px;
    display: flex;
    align-items: center;
    gap: 12px;
    font-weight: 700;
    font-size: 30px;
    letter-spacing: 0.5px;
    color: var(--ink);
    text-transform: uppercase;
  }
  .brand__dot {
    width: 24px; height: 24px; border-radius: 50%;
    background: var(--green);
  }
  .person__name {
    position: absolute; left: 30px; top: 152px;
    font-size: 24px; font-weight: 500; color: var(--green);
    letter-spacing: 0.3px;
  }
  .person__role {
    position: absolute; left: 30px; top: 183px;
    font-size: 17px; color: var(--ink);
  }
  .divider {
    position: absolute; left: 30px; top: 213px;
    width: 552px; height: 1px; background: var(--rule);
  }
  .contact {
    position: absolute; left: 30px; top: 223px;
    list-style: none;
  }
  .contact__item {
    display: flex; align-items: center; gap: 12px;
    height: 25px; font-size: 16.5px; color: var(--grey);
  }
  .contact__item svg { width: 14px; height: 16px; flex: none; }
  .web-band {
    position: absolute; left: 0; top: 287px;
    width: 100%; height: 37px; background: var(--green-band);
  }
  .web-band__url {
    position: absolute; left: 30px; top: 0; line-height: 37px;
    font-size: 16.5px; font-weight: 500; color: var(--white);
    letter-spacing: 1.6px;
  }
  .web-band__corner { position: absolute; right: 0; top: 0; width: 72px; height: 37px; }

  /* back */
  .pitch { position: absolute; left: 45px; top: 63px; color: var(--ink); }
  .pitch__title { font-size: 18px; font-weight: 500; text-transform: uppercase; }
  .pitch__list { list-style: none; margin-top: 8px; }
  .pitch__list li {
    position: relative; padding-left: 18px;
    font-size: 16.5px; line-height: 26px;
  }
  .pitch__list li::before {
    content: ""; position: absolute; left: 2px; top: 10px;
    width: 6px; height: 6px; border-radius: 50%; background: var(--ink);
  }
  .pitch__cta {
    margin-top: 10px;
    font-family: "Roboto Condensed", Arial, sans-serif;
    font-weight: 700; font-size: 16px;
  }
  .offer { position: absolute; left: 45px; top: 212px; color: var(--ink); }
  .offer__headline {
    font-family: "Archivo Black", Arial, sans-serif;
    font-size: 44px; line-height: 50px; letter-spacing: 0.5px;
  }
  .offer__detail {
    font-family: "Archivo Black", Arial, sans-serif;
    font-size: 19.5px; line-height: 26px; letter-spacing: 0.3px;
  }
</style>
</head>
<body>
  <section class="card card--front" aria-label="Business card front">
    <div class="brand"><span class="brand__dot"></span>Steady Ledger</div>
    <h1 class="person__name">DANIEL R. HAYES</h1>
    <p class="person__role">Personal Financial Coach</p>
    <div class="divider"></div>
    <ul class="contact">
      <li class="contact__item">
        <svg viewBox="0 0 14 16" aria-hidden="true"><rect x="2.5" y="0.8" width="9" height="14.4" rx="1.5" fill="none" stroke="#2f9e44" stroke-width="1.6"/><rect x="5" y="12.2" width="4" height="1.2" fill="#2f9e44"/></svg>
        (205) 555-0187
      </li>
      <li class="contact__item">
        <svg viewBox="0 0 14 16" aria-hidden="true"><rect x="0.5" y="4" width="13" height="9" fill="#2f9e44"/><path d="M0.5 4 L7 9 L13.5 4" fill="none" stroke="#fff" stroke-width="1.2"/></svg>
        daniel@steadyledgercoach.com
      </li>
    </ul>
    <div class="web-band">
      <span class="web-band__url">www.steadyledgercoach.com</span>
      <svg class="web-band__corner" viewBox="0 0 72 37" aria-hidden="true">
        <path d="M72 0 L40 0 Q18 20 0 37 L72 37 Z" fill="#000"/>
      </svg>
    </div>
  </section>

  <section class="card card--back" aria-label="Business card back">
    <div class="pitch">
      <h2 class="pitch__title">Struggling with your finances?</h2>
      <ul class="pitch__list">
        <li>Learn to become debt free</li>
        <li>Discover the power of cash</li>
        <li>Control your money instead of it controlling you</li>
      </ul>
      <p class="pitch__cta">Let us help you achieve a new level of financial freedom!</p>
    </div>
    <div class="offer">
      <p class="offer__headline">SPECIAL OFFER!</p>
      <p class="offer__detail">FREE 30 MINUTE CONSULTATION</p>
    </div>
  </section>
</body>
</html>
```